Support People to improve their image and well-being by provided personalised advise

We need a design for business cards that could be used for production on plano press. We build a new business in our region for advising mostly women (also men though) on style embracing several aspects including fashion, style, self-confidence and ultimately your internal and external image. The business card should be "classy", "french-style". The business is located in the french -speaking part of Switzerland, close to France. The name of the company is Lomu Grace

Target Market(s)

Service fees won't be cheap (medium to premium) thus we target mid-class to upper-class women (1st target) and men (2nd target)

Industry/Entity Type

Life Coaching

Contact Information for Business Card

Conseil en Image

+41 76 418 63 07
tovasel@lomu-grace.example
profil.example/in/sel-moran-tova

Logo Text

Lomu Grace

Colors

Designer to choose colors to be used in the design.

```html
<!DOCTYPE html>
<html lang="fr">
<head>
<meta charset="utf-8">
<title>Lomu Grace – Carte de visite</title>
<link rel="stylesheet" href="https://fonts.googleapis.com/css2?family=Lato:wght@400&family=Pinyon+Script&display=swap">
<style>
  :root {
    --stage: #070707;
    --paper: #ffffff;
    --plum: #6e1f6c;
    --orchid: #a62ea4;
    --magenta: #ac1cad;
    --magenta-deep: #8e1a88;
    --magenta-mid: #a01c9c;
    --ink: #222222;
    --rule: #555555;
  }
  * { box-sizing: border-box; margin: 0; padding: 0; }
  html, body {
    width: 1200px; height: 900px; overflow: hidden;
    background: var(--stage);
  }
  .canvas { position: relative; width: 1200px; height: 900px; }
  .card {
    position: absolute; top: 170px;
    width: 347px; height: 561px; overflow: hidden;
  }
  .card--front { left: 259px; background: var(--paper); }
  .card--back { left: 631px; background: var(--magenta); }

  .card__backdrop {
    position: absolute; inset: 0;
    background: linear-gradient(135deg, var(--magenta-deep) 0%, var(--magenta) 50%, var(--magenta-deep) 100%);
  }

  .brand {
    position: absolute; left: 0; right: 0;
    display: flex; align-items: center; justify-content: center; gap: 12px;
    font-family: "Lato", sans-serif; font-weight: 400;
    white-space: nowrap;
  }
  .brand__mark { display: block; }
  .card--front .brand { top: 146px; font-size: 40px; color: var(--plum); }
  .card--front .brand__mark { width: 26px; height: 26px; background: var(--orchid); }
  .card--back .brand { top: 258px; font-size: 44px; color: var(--paper); }
  .card--back .brand__mark { width: 28px; height: 28px; background: var(--paper); }

  .contact {
    position: absolute; left: 0; right: 0; top: 322px;
    text-align: center; font-family: "Lato", sans-serif; color: var(--ink);
  }
  .contact__name {
    font-family: "Pinyon Script", cursive; font-weight: 400;
    font-size: 38px; line-height: 1; color: var(--plum);
  }
  .contact__role { font-size: 15px; margin-top: 4px; }
  .rule { width: 193px; height: 1px; background: var(--rule); margin: 14px auto 0; }
  .contact__lines { font-size: 15px; line-height: 21px; margin-top: 17px; }
  .profile-divider {
    position: relative; width: 193px; height: 22px; margin: 19px auto 0;
  }
  .profile-divider::before {
    content: ""; position: absolute; left: 0; right: 0; top: 11px;
    height: 1px; background: var(--rule);
  }
  .profile-divider__dot {
    position: absolute; left: 86px; top: 1px;
    width: 20px; height: 20px; border-radius: 50%; background: var(--orchid);
  }
  .contact__profile { font-size: 15px; margin-top: 6px; }
</style>
</head>
<body>
<main class="canvas">
  <section class="card card--front" aria-label="Recto">
    <div class="brand"><span class="brand__mark"></span>Lomu Grace</div>
    <div class="contact">
      <p class="contact__name">Julien Marceau</p>
      <p class="contact__role">Managing Director</p>
      <div class="rule"></div>
      <p class="contact__lines">+41 76 418 63 07<br>tovasel@lomu-grace.example</p>
      <div class="profile-divider"><span class="profile-divider__dot"></span></div>
      <p class="contact__profile">profil.example/in/sel-moran-tova</p>
    </div>
  </section>

  <section class="card card--back" aria-label="Verso">
    <div class="card__backdrop" role="img" aria-label="Motif géométrique diagonal en tons magenta et prune"></div>
    <div class="brand"><span class="brand__mark"></span>Lomu Grace</div>
  </section>
</main>
</body>
</html>
```